Brochure for Brindle Lifelong Learning Institute

Design an eye-catching brochure (both sides, tri-folded) to get new members to join our group - the Brindle Lifelong Learning Institute at MVCT. I've included a very rough draft PDF along with photos and links to our website and facebook page for more artwork if needed. Check out http://mvct-brindle.notepagehub.example/speakers for more verbiage if needed

Target Market(s)

Seniors 55 years +

Industry/Entity Type

Learning

Requirements
Must have
• A call for action! An area with Name, Address and credit card number so they can send enrollment fee in....
Nice to have
• Color, attractive faces, excellent design....

```html
<!DOCTYPE html>
<html lang="en">
<head>
<meta charset="utf-8">
<title>Brindle Lifelong Learning Institute – Tri-fold Brochure</title>
<link rel="stylesheet" href="https://fonts.googleapis.com/css2?family=Tinos:ital,wght@0,400;0,700;1,400&display=swap">
<style>
  :root{
    --bg:#1d1d1f;
    --sun:#f8cc1b;
    --orange:#ef8a1e;
    --blue:#1f6fc0;
    --blue-deep:#174f9a;
    --red:#c4161c;
    --ink:#1c2b4a;
    --white:#ffffff;
    --cell:#fde84a;
    --field:rgba(255,255,255,.6);
  }
  *{box-sizing:border-box;margin:0;padding:0}
  html,body{width:1200px;height:900px;overflow:hidden;background:var(--bg)}
  body{position:relative;font-family:"Tinos","Times New Roman",serif;color:var(--ink)}
  .sheet{position:absolute;top:225px;width:570px;height:450px;overflow:hidden;box-shadow:0 6px 18px rgba(0,0,0,.5)}
  .sheet--outside{left:20px}
  .sheet--inside{left:610px}
  .sheet__art{position:absolute;inset:0;width:570px;height:450px}
  .panel{position:absolute;top:0;width:190px;height:450px;padding:0 12px}
  .panel--1{left:0}.panel--2{left:190px}.panel--3{left:380px}
  .bar{background:var(--blue);color:var(--white);font-weight:700;font-size:8px;padding:3px 6px;border:1px solid var(--white)}
  .bar--title{font-size:11px;text-transform:uppercase;letter-spacing:.5px;color:var(--white);font-weight:400}

  /* outside: members panel */
  .members{position:absolute;left:14px;top:92px;width:162px}
  .members table{width:100%;border-collapse:collapse;font-size:6.5px;margin-top:4px}
  .members th,.members td{background:var(--cell);border:1px solid var(--blue-deep);padding:2px 3px;text-align:left}
  .members th{font-weight:700;color:var(--blue-deep)}
  .photo-grid{position:absolute;left:14px;top:262px;width:162px;height:150px;border:3px solid var(--white);display:grid;grid-template-columns:1fr 1fr;grid-template-rows:1fr 1fr;gap:3px;background:var(--white)}
  .photo{background:linear-gradient(135deg,#8a6a55,#c9a58a 55%,#5a6a7a)}
  .photo--wide{grid-column:1 / 3;background:linear-gradient(135deg,#3c5a80,#c7a384 50%,#d8d4cf)}
  .photo--crowd{background:linear-gradient(135deg,#7b8797,#b99b85)}

  /* outside: info panel */
  .info{padding:38px 10px 0 22px}
  .info__lead{color:var(--red);font-weight:700;font-size:6.5px;margin:6px 0 5px;line-height:1.3}
  .info ul{list-style:none;font-size:6.3px;color:var(--red);line-height:1.3}
  .info li{position:relative;padding-left:7px;margin-bottom:3px}
  .info li::before{content:"";position:absolute;left:0;top:2px;width:3.5px;height:3.5px;border-radius:50%;background:var(--red)}
  .info__contact{font-size:6.3px;color:var(--red);font-weight:700;line-height:1.35;margin-top:3px}
  .info__note{font-size:6.3px;color:var(--red);line-height:1.35;margin-top:4px}
  .enroll{margin-top:6px;border:1px solid var(--blue);background:var(--field);padding:3px 5px 4px}
  .enroll__title{font-size:7px;font-weight:700;color:var(--blue-deep);text-transform:uppercase;letter-spacing:.3px}
  .enroll__text{font-size:5.8px;color:var(--ink);line-height:1.3;margin:1px 0 2px}
  .field{display:flex;align-items:flex-end;gap:3px;font-size:6px;color:var(--blue-deep);font-weight:700;height:10px}
  .field__line{flex:1;border-bottom:1px solid var(--blue-deep);height:7px}
  .field-row{display:flex;gap:6px}
  .field-row .field{flex:1}

  /* outside: cover */
  .cover-photo{position:absolute;left:412px;top:10px;width:174px;height:310px;border-radius:0 0 0 60px;background:linear-gradient(160deg,#6e7f5a,#c49a7e 45%,#e8cdb8 65%,#7a5d8a)}
  .brand{position:absolute;left:388px;top:348px;width:182px;height:40px;background:#fff7c2;border-top:3px solid var(--blue);border-bottom:3px solid var(--blue);display:flex;align-items:center;gap:6px;padding:0 8px}
  .brand__mark{width:22px;height:22px;border-radius:50%;background:var(--blue-deep);flex:none}
  .brand__name{font-size:9px;font-weight:700;color:var(--blue-deep);line-height:1.1}

  /* inside */
  .inside-text{font-size:6.5px;color:var(--ink);line-height:1.35}
  .classes{padding-top:76px}
  .classes .bar--title{margin-bottom:4px}
  .classes h3,.board h3,.about h3{font-size:7.5px;color:var(--red);font-weight:700;margin-bottom:4px;line-height:1.2}
  .course{margin-top:6px}
  .course__title{display:block}
  .course__teacher{display:block;color:var(--red);font-style:italic}
  .board{padding-top:68px}
  .board .bar--title{text-align:center;margin-bottom:8px}
  .board h3{text-align:center}
  .board__photo{height:92px;border:3px solid #e07a5f;background:linear-gradient(135deg,#6f8f5a,#c7a98c 45%,#b23a3a 60%,#d9d3c4);margin:4px 0 8px}
  .roster{list-style:none}
  .roster li{margin-bottom:1.5px}
  .roster em{color:var(--red);font-style:normal}
  .about{padding-top:120px}
  .about p{margin-bottom:6px}
</style>
</head>
<body>

<section class="sheet sheet--outside" aria-label="Brochure outside spread">
  <svg class="sheet__art" viewBox="0 0 570 450" aria-hidden="true">
    <defs>
      <linearGradient id="sunFill" x1="0" y1="0" x2="1" y2="1">
        <stop offset="0" stop-color="#fbd51c"/><stop offset="1" stop-color="#f6b81a"/>
      </linearGradient>
    </defs>
    <rect width="570" height="450" fill="url(#sunFill)"/>
    <path d="M0 0H190V30C130 40 60 70 0 120Z" fill="#f08a1e"/>
    <path d="M0 0H190V12C120 20 50 50 0 92Z" fill="#1f6fc0"/>
    <path d="M0 450H190V420C120 420 60 435 0 450Z" fill="#1f6fc0"/>
    <path d="M190 0H198V450H190Z" fill="#1f6fc0"/>
    <path d="M198 0H207V450H198Z" fill="#f08a1e"/>
    <path d="M380 405C330 425 270 438 207 444V450H380Z" fill="#1f6fc0"/>
    <path d="M380 390C330 410 270 424 207 430V440C270 434 330 420 380 400Z" fill="#f08a1e"/>
    <path d="M380 0H570V330C480 340 420 300 390 240C370 180 372 80 400 0Z" fill="#1f6fc0"/>
    <path d="M380 0H396C372 80 372 200 400 260C420 305 480 345 570 345V360C470 362 410 320 385 250Z" fill="#f08a1e"/>
    <line x1="190" y1="0" x2="190" y2="450" stroke="rgba(0,0,0,.12)"/>
    <line x1="380" y1="0" x2="380" y2="450" stroke="rgba(0,0,0,.12)"/>
  </svg>

  <div class="members">
    <div class="bar">Members</div>
    <table>
      <thead><tr><th>Name</th><th>Member Since</th><th>Types</th></tr></thead>
      <tbody>
        <tr><td>Carla Dunmore</td><td>Sep 18, 2009</td><td>Organizer</td></tr>
        <tr><td>Dora Wexley</td><td>Aug 14, 2012</td><td>Organizer</td></tr>
        <tr><td>Dale Hutton</td><td>Aug 29, 2009</td><td>Member</td></tr>
        <tr><td>Iris Loman</td><td>Sep 8, 2010</td><td>Member</td></tr>
        <tr><td>Magda Frey</td><td>Oct 26, 2008</td><td>Organizer</td></tr>
        <tr><td>Ruth Halvorsen</td><td>Jan 6, 2014</td><td>Organizer</td></tr>
        <tr><td>Pam Ostrow</td><td>Oct 3, 2008</td><td>Member</td></tr>
        <tr><td>Zelda Moor</td><td>Oct 9, 2006</td><td>Organizer</td></tr>
      </tbody>
    </table>
  </div>
  <div class="photo-grid">
    <div class="photo" role="img" aria-label="Photo of members at a social event"></div>
    <div class="photo photo--crowd" role="img" aria-label="Photo of a full lecture hall"></div>
    <div class="photo photo--wide" role="img" aria-label="Photo of three members smiling together"></div>
  </div>

  <div class="panel panel--2 info">
    <div class="bar">Information for Members and Visitors</div>
    <p class="info__lead">Anyone with a love of learning is welcome to join us at our weekly classes and talks.</p>
    <ul>
      <li>All ages and backgrounds welcome.</li>
      <li>No exams.</li>
      <li>Modest annual fee.</li>
      <li>Weekday mornings, 10:00 to noon, in the campus lecture hall.</li>
      <li>Members may bring a guest to any two sessions each term.</li>
      <li>Parking passes are available for a small daily fee; arrive early.</li>
      <li>Questions? Contact our office below.</li>
    </ul>
    <p class="info__contact">Email: hello@brindle-mvct.example<br>Phone: 408-555-0174</p>
    <p class="info__note"><strong>Program Guide</strong> – made possible by the volunteers who plan our courses.</p>
    <div class="enroll" aria-label="Enrollment form">
      <p class="enroll__title">Join Us – Enrollment</p>
      <p class="enroll__text">Fill in and mail with your annual fee to the office.</p>
      <div class="field">Name <span class="field__line"></span></div>
      <div class="field">Address <span class="field__line"></span></div>
      <div class="field">City / Zip <span class="field__line"></span></div>
      <div class="field">Card No. <span class="field__line"></span></div>
      <div class="field-row">
        <div class="field">Exp. <span class="field__line"></span></div>
        <div class="field">CVV <span class="field__line"></span></div>
      </div>
    </div>
  </div>

  <div class="cover-photo" role="img" aria-label="Photo of two smiling members of the institute"></div>
  <div class="brand">
    <span class="brand__mark"></span>
    <span class="brand__name">Mid Valley College of Technology</span>
  </div>
</section>

<section class="sheet sheet--inside" aria-label="Brochure inside spread">
  <svg class="sheet__art" viewBox="0 0 570 450" aria-hidden="true">
    <defs>
      <linearGradient id="skyFill" x1="0" y1="0" x2="0" y2="1">
        <stop offset="0" stop-color="#8fd0f3"/><stop offset="1" stop-color="#4aa6e2"/>
      </linearGradient>
      <linearGradient id="sunCorner" x1="0" y1="0" x2="1" y2="1">
        <stop offset="0" stop-color="#fbd51c"/><stop offset="1" stop-color="#f08a1e"/>
      </linearGradient>
    </defs>
    <rect width="570" height="450" fill="url(#skyFill)"/>
    <path d="M0 0H190V40C120 40 50 55 0 80Z" fill="url(#sunCorner)"/>
    <path d="M0 80C50 55 120 42 190 45V60C120 56 55 70 0 95Z" fill="#1f6fc0"/>
    <path d="M190 0H380V30H190Z" fill="url(#sunCorner)"/>
    <path d="M190 30H380V52H190Z" fill="#1f6fc0"/>
    <path d="M190 390C250 415 320 425 380 415V450H190Z" fill="url(#sunCorner)"/>
    <path d="M190 378C250 405 320 413 380 403V417C320 428 250 420 190 398Z" fill="#1f6fc0"/>
    <path d="M380 0H570V70C500 60 430 80 380 110Z" fill="url(#sunCorner)"/>
    <path d="M380 110C430 80 500 62 570 72V90C500 80 430 98 380 128Z" fill="#1f6fc0"/>
    <line x1="190" y1="0" x2="190" y2="450" stroke="rgba(0,0,0,.12)"/>
    <line x1="380" y1="0" x2="380" y2="450" stroke="rgba(0,0,0,.12)"/>
  </svg>

  <div class="panel panel--1 classes inside-text">
    <div class="bar--title">Classes</div>
    <h3>Academic Year 2014 – 2015 Courses</h3>
    <p>Our classes are taught by faculty and guest experts and meet weekly through the year. Each course runs four to six sessions.</p>
    <p style="margin-top:5px">The courses are open to all members; no prior study is needed. Many sessions include time for questions and lively discussion with the speaker.</p>
    <div class="course"><span class="course__title">Reading the Classics Again</span><span class="course__teacher">Prof. Ellen Marsh</span></div>
    <div class="course"><span class="course__title">Stories of the Coast Ranges</span><span class="course__teacher">Prof. Hal Renner</span></div>
    <div class="course"><span class="course__title">Science of Our Changing Bay</span><span class="course__teacher">Prof. Lydia Crane</span></div>
    <div class="course"><span class="course__title">Music and Memory Series</span><span class="course__teacher">Prof. Ada Tillman</span></div>
    <div class="course"><span class="course__title">World Religions in Brief</span><span class="course__teacher">Prof. Sam Ortega</span></div>
    <div class="course"><span class="course__title">History of Writing</span><span class="course__teacher">Prof. Nora Quill</span></div>
    <div class="course"><span class="course__title">Art of the Modern Age</span><span class="course__teacher">Prof. Jude Varga</span></div>
  </div>

  <div class="panel panel--2 board inside-text">
    <div class="bar--title">Board of Directors</div>
    <h3>Brindle Lifelong Learning Institute at MVCT<br>Board, 2014 – 2015</h3>
    <div class="board__photo" role="img" aria-label="Group photo of the board of directors"></div>
    <ul class="roster">
      <li>President: <em>Ruth Halvorsen</em></li>
      <li>Vice President: <em>Carla Dunmore</em></li>
      <li>Recording Secretary: <em>Iris Loman</em></li>
      <li>Treasurer: <em>Dale Hutton</em></li>
      <li>Past President: <em>Magda Frey</em></li>
      <li>Program Chair: <em>Pam Ostrow</em></li>
      <li>Program Co-Chair: <em>Gil Sorensen</em></li>
      <li>Membership: <em>Zelda Moor</em></li>
      <li>Hospitality: <em>Dora Wexley</em></li>
      <li>Publicity: <em>Ned Atwater</em></li>
      <li>Newsletter: <em>June Pell</em></li>
      <li>Audio Visual: <em>Walt Brennan</em></li>
      <li>Campus Liaison: <em>Rita Soto</em></li>
    </ul>
  </div>

  <div class="panel panel--3 about inside-text">
    <h3>About the Brindle Lifelong Learning Institute at MVCT</h3>
    <p>The Brindle Lifelong Learning Institute at MVCT is a member-led community of adults who share a love of learning. We offer lectures, courses and gatherings for curious minds.</p>
    <p>Membership is open to everyone aged 55 and over. Members attend classes, join discussion groups and enjoy friendly social events through the year.</p>
    <p>Speakers are listed at<br>http://mvct-brindle.notepagehub.example/speakers</p>
    <h3>History of the Lifelong Learning Organization at MVCT</h3>
    <p>Our group began as a small circle of retired faculty and friends and has grown into a lively institute with hundreds of members.</p>
  </div>
</section>

</body>
</html>
```